Home page design for Drone video business (the Business focusses on home videos for realtors)

Dear reader,

*I NEED DESIGNS OF ALL THE PAGES*
We need a first design of a homepage and of 4 other pages of the website of a business that sells drone video services. All the pages will need to be in the similar design style.
The video's are targeted at consumers that want to sell there home and would like to have a cool drone video of photos of their home.

How does the website look:
- has a navbar on top
- A cool looking banner of an areal drone.
- A Big header: with company name: SkyLoftReels
- A smaller subheader: We film your home to increase your chances of sale
- Then a section with a Big header: How does it work
- In this section a place for a vimeo explainitory video
- Then a similar navbar styled bar with a phone number and a email address
- Then a section where the videos porfolio is displayed in a cool way
- Inside this sectiona header: Our work

- A section with header: Why us?
- 4 symbols here with a subheader and some lorum ipsum text underneath (see wireframe images)

- Under that a: Contact us
- where you can put in name, email, phone, message box and a send button

- At the bottom a footer with phone number and a fake address for now.

Be creative. Use creative but serious color.
Use a serious font. Make it a sharp design. Sharp lines. Not to dark design and not to light design.

The wireframes are the same kind of images.
PLEASE PUT IN DESIGNS OF ALL THE PAGES

Good luck

Target Market(s)

People that want to sell home and want to make a cool drone video or photos of their home.

Industry/Entity Type

Business

Contact Information for Business Card

Lucas Wenning
lucas@skyloftreels.example
+31647208351

Logo Text

SkyLoftReels

Number of Pages Required

1 page

Font styles to use
Sans Serif

Requirements
Must have
• All the sections as explained in the instructions.
• The nav bar should have an about us, services, portfolio and a contact us buttons.
• See instruction for details.
• Must include designs of the front page, contact us, our services, portfolio and contact us.
• If you do add some designs for the "about us", "services", "prices", "portfolio" and "contact us" pages, you make a way better chance of winning the competition.
Nice to have
• designs for the other pages as described at the Must haves. You make a better chance of winning if you include them. Look at the wireframes to see the mockups for those pages. think creative about what kind of sections and design should be included in those pages.
Should not have
• bad designs.

```html
<!DOCTYPE html>
<html lang="en">
<head>
<meta charset="utf-8">
<title>SkyLoftReels</title>
<link href="https://fonts.googleapis.com/css2?family=Noto+Serif:wght@400;700&family=Open+Sans:wght@400;600;700&display=swap" rel="stylesheet">
<style>
:root{
  --red:#e8493b;
  --red-dark:#d63a2b;
  --ink:#3a3a3a;
  --muted:#8a8a8a;
  --dark:#1c1c1c;
  --darker:#151515;
  --footer:#232323;
  --white:#ffffff;
  --serif:"Noto Serif", Georgia, serif;
  --sans:"Open Sans", Arial, sans-serif;
}
*{box-sizing:border-box;margin:0;padding:0}
html,body{width:1200px;height:2267px;overflow:hidden}
body{font-family:var(--sans);color:var(--ink);background:var(--white);position:relative}
.wrap{position:relative;width:1200px}

/* hero */
.hero{position:relative;height:615px;background:linear-gradient(180deg,#8d9197 0%,#b4b7bb 40%,#a9a9ab 70%,#6f6d6c 100%)}
.hero-media{position:absolute;inset:0}
.topbar{position:absolute;top:0;left:0;right:0;height:80px;background:rgba(40,40,40,.72);display:flex;align-items:center;justify-content:space-between;padding:0 133px}
.brand{font-family:var(--serif);font-weight:700;font-size:40px;color:var(--white);letter-spacing:1px}
.menu{display:flex;gap:28px;list-style:none}
.menu a{font-size:12px;color:var(--white);text-decoration:none;font-weight:600}
.menu a.active{text-decoration:underline}
.hero-title{position:absolute;top:262px;width:100%;text-align:center;font-family:var(--serif);font-weight:700;font-size:64px;color:var(--white)}
.hero-sub{position:absolute;top:338px;width:100%;text-align:center;font-size:16px;color:var(--white)}
.dots{position:absolute;top:581px;left:0;right:0;display:flex;justify-content:center;gap:16px}
.dots span{width:9px;height:9px;border-radius:50%;background:var(--white)}
.dots span.on{background:transparent;border:2px solid var(--white)}

/* how it works */
.how{position:relative;height:533px;background:linear-gradient(180deg,#f4f4f4,#f8f8f8)}
.section-title{font-family:var(--serif);font-weight:400;font-size:40px;color:var(--red);text-align:center}
.how .section-title{padding-top:66px}
.video{position:absolute;left:320px;top:139px;width:560px;height:319px;background:linear-gradient(135deg,#6b5a48,#8f7b66 50%,#4e6578);display:flex;align-items:center;justify-content:center}

/* contact band */
.band{display:flex;height:80px}
.band div{flex:1;display:flex;align-items:center;justify-content:center;gap:10px;font-family:var(--serif);font-size:27px;color:var(--white)}
.band .phone{background:var(--red)}
.band .mail{background:var(--red-dark)}

/* work */
.work{position:relative;height:295px;background:linear-gradient(180deg,#3a3a3a,#2b2b2b)}
.work .section-title{color:var(--white);font-size:38px;padding-top:12px}
.thumb{position:absolute;top:79px;height:209px;display:flex;align-items:center;justify-content:center}
.t1{left:133px;width:308px;background:linear-gradient(180deg,#7d93ad,#a48b4e 60%,#556b3c)}
.t2{left:447px;width:307px;background:linear-gradient(180deg,#8ea3b4,#6b7a5e 45%,#4f8a3a)}
.t3{left:759px;width:308px;background:linear-gradient(180deg,#5b7fa7,#7f8d96 50%,#a86a52)}
.arrow{position:absolute;top:139px}
.arrow.left{left:54px}
.arrow.right{left:1127px}

/* why */
.why{position:relative;height:320px;background:var(--white)}
.why .section-title{padding-top:28px}
.feature{position:absolute;width:420px}
.feature .icon{position:absolute;left:0;top:0;width:64px;height:64px;border-radius:50%;background:#3d3d3d;display:flex;align-items:center;justify-content:center}
.feature h3{position:absolute;left:73px;top:-4px;font-family:var(--serif);font-weight:400;font-size:24px;color:var(--ink);white-space:nowrap}
.feature p{position:absolute;left:73px;top:31px;width:355px;font-size:10.5px;line-height:15px;color:var(--muted)}
.f1{left:131px;top:106px}.f2{left:642px;top:106px}
.f3{left:131px;top:210px}.f4{left:642px;top:210px}

/* contact form */
.contact{height:263px;background:var(--dark);padding-top:35px}
.contact h2{text-align:center;font-size:22px;font-weight:700;color:var(--red)}
.fields{display:flex;gap:11px;padding:0 133px;margin-top:20px}
.field{flex:1;height:41px;border:1px solid #555;font-size:11px;color:#bbb;padding:0 15px;display:flex;align-items:center}
.field.wide{margin:14px 133px 0;height:42px}
.submit{display:block;margin:20px auto 0;width:68px;height:35px;background:var(--red);color:var(--white);font-size:10px;font-weight:600;border:none;font-family:var(--sans)}

/* footer */
.info{height:80px;background:var(--footer);display:flex;align-items:center;justify-content:space-between;padding:0 133px;font-size:15.5px;color:#9a9a9a}
.info span{display:flex;align-items:center;gap:10px}
.legal{height:81px;background:var(--darker);display:flex;align-items:center;justify-content:space-between;padding:0 133px;font-size:11px;color:#aaa}
.social{display:flex;gap:14px}
.social span{width:9px;height:9px;border-radius:50%;background:#ddd}
</style>
</head>
<body>
<div class="wrap">

<header class="hero">
  <div class="hero-media" role="img" aria-label="White quadcopter drone hovering above a hazy city skyline"></div>
  <nav class="topbar">
    <div class="brand">SLR</div>
    <ul class="menu">
      <li><a class="active" href="#">SERVICES</a></li>
      <li><a href="#">ABOUT US</a></li>
      <li><a href="#">PORTFOLIO</a></li>
      <li><a href="#">CONTACT</a></li>
    </ul>
  </nav>
  <h1 class="hero-title">SkyLoftReels</h1>
  <p class="hero-sub">We film your home to increase your chances of sale</p>
  <div class="dots"><span class="on"></span><span></span><span></span><span></span></div>
</header>

<section class="how">
  <h2 class="section-title">How does it work?</h2>
  <div class="video" role="img" aria-label="Explainer video: tablet showing aerial city footage beside a drone on a wooden table">
    <svg width="60" height="60" viewBox="0 0 60 60"><circle cx="30" cy="30" r="27" fill="none" stroke="#fff" stroke-width="4"/><path d="M24 18 L42 30 L24 42Z" fill="#fff"/></svg>
  </div>
</section>

<section class="band">
  <div class="phone">
    <svg width="22" height="22" viewBox="0 0 24 24"><path fill="#fff" d="M6.6 10.8a15 15 0 0 0 6.6 6.6l2.2-2.2c.3-.3.7-.4 1-.2 1.1.4 2.3.6 3.6.6.6 0 1 .4 1 1V20c0 .6-.4 1-1 1A17 17 0 0 1 3 4c0-.6.4-1 1-1h3.5c.6 0 1 .4 1 1 0 1.3.2 2.5.6 3.6.1.3 0 .7-.2 1z"/></svg>
    +31647208351
  </div>
  <div class="mail">
    <svg width="24" height="18" viewBox="0 0 24 18"><rect width="24" height="18" rx="2" fill="#fff"/><path d="M1 2 L12 10 L23 2" fill="none" stroke="#d63a2b" stroke-width="2"/></svg>
    contact@skyloftreels.example
  </div>
</section>

<section class="work">
  <h2 class="section-title">Our work</h2>
  <svg class="arrow left" width="18" height="28" viewBox="0 0 18 28"><path d="M14 3 L4 14 L14 25" fill="none" stroke="#999" stroke-width="2.5"/></svg>
  <div class="thumb t1" role="img" aria-label="Aerial view of a large yellow house with gardens">
    <svg width="58" height="58" viewBox="0 0 60 60"><circle cx="30" cy="30" r="27" fill="none" stroke="#fff" stroke-width="4"/><path d="M24 18 L42 30 L24 42Z" fill="#fff"/></svg>
  </div>
  <div class="thumb t2" role="img" aria-label="Aerial view of a city park with green lawns">
    <svg width="58" height="58" viewBox="0 0 60 60"><circle cx="30" cy="30" r="27" fill="none" stroke="#fff" stroke-width="4"/><path d="M24 18 L42 30 L24 42Z" fill="#fff"/></svg>
  </div>
  <div class="thumb t3" role="img" aria-label="Aerial view of a dense town with colourful rooftops">
    <svg width="58" height="58" viewBox="0 0 60 60"><circle cx="30" cy="30" r="27" fill="none" stroke="#fff" stroke-width="4"/><path d="M24 18 L42 30 L24 42Z" fill="#fff"/></svg>
  </div>
  <svg class="arrow right" width="18" height="28" viewBox="0 0 18 28"><path d="M4 3 L14 14 L4 25" fill="none" stroke="#999" stroke-width="2.5"/></svg>
</section>

<section class="why">
  <h2 class="section-title">Why us?</h2>
  <div class="feature f1">
    <div class="icon"><svg width="26" height="18" viewBox="0 0 26 18"><rect x="1" y="1" width="24" height="16" rx="2" fill="none" stroke="#fff" stroke-width="2"/><circle cx="13" cy="9" r="4" fill="#fff"/></svg></div>
    <h3>Cheap</h3>
    <p>Proin ultricies feugiat urna. Duis sodales tincidunt vehicula. Suspendisse quis quam ante. Nam ac blandit odio.</p>
  </div>
  <div class="feature f2">
    <div class="icon"><svg width="24" height="24" viewBox="0 0 24 24"><circle cx="12" cy="12" r="7" fill="none" stroke="#fff" stroke-width="4" stroke-dasharray="3 2.5"/><circle cx="12" cy="12" r="3" fill="#fff"/></svg></div>
    <h3>Flexible</h3>
    <p>Proin ultricies feugiat urna. Duis sodales tincidunt vehicula. Suspendisse quis quam ante. Nam ac blandit odio.</p>
  </div>
  <div class="feature f3">
    <div class="icon"><svg width="22" height="22" viewBox="0 0 22 22"><rect x="1" y="9" width="5" height="12" fill="#fff"/><path d="M8 9 L12 2 C14 2 14 4 13.5 7 L20 7 C21 7 21.5 8 21 9 L18 20 H8Z" fill="#fff"/></svg></div>
    <h3>Quality</h3>
    <p>Proin ultricies feugiat urna. Duis sodales tincidunt vehicula. Suspendisse quis quam ante. Nam ac blandit odio.</p>
  </div>
  <div class="feature f4">
    <div class="icon"><svg width="24" height="20" viewBox="0 0 24 20"><path d="M2 1 V19 H23" fill="none" stroke="#fff" stroke-width="2"/><path d="M5 15 L10 9 L14 12 L21 4" fill="none" stroke="#fff" stroke-width="2.5"/></svg></div>
    <h3>Increase sales changes</h3>
    <p>Proin ultricies feugiat urna. Duis sodales tincidunt vehicula. Suspendisse quis quam ante. Nam ac blandit odio.</p>
  </div>
</section>

<section class="contact">
  <h2>CONTACT US</h2>
  <div class="fields">
    <div class="field">Name</div>
    <div class="field">Email</div>
    <div class="field">Phone</div>
    <div class="field">Address</div>
  </div>
  <div class="field wide">Comments</div>
  <button class="submit">SUBMIT</button>
</section>

<footer>
  <div class="info">
    <span><svg width="11" height="15" viewBox="0 0 12 16"><path d="M6 0a6 6 0 0 0-6 6c0 4.5 6 10 6 10s6-5.5 6-10a6 6 0 0 0-6-6zm0 8.5A2.5 2.5 0 1 1 6 3.5a2.5 2.5 0 0 1 0 5z" fill="#9a9a9a"/></svg>24 Building name Street name, City Zipcode</span>
    <span><svg width="14" height="14" viewBox="0 0 24 24"><path fill="#9a9a9a" d="M6.6 10.8a15 15 0 0 0 6.6 6.6l2.2-2.2c.3-.3.7-.4 1-.2 1.1.4 2.3.6 3.6.6.6 0 1 .4 1 1V20c0 .6-.4 1-1 1A17 17 0 0 1 3 4c0-.6.4-1 1-1h3.5c.6 0 1 .4 1 1 0 1.3.2 2.5.6 3.6.1.3 0 .7-.2 1z"/></svg>Phone &nbsp;: +31647208351</span>
    <span><svg width="17" height="13" viewBox="0 0 24 18"><rect width="24" height="18" rx="2" fill="#9a9a9a"/><path d="M1 2 L12 10 L23 2" fill="none" stroke="#232323" stroke-width="2"/></svg>Email : contact@skyloftreels.example</span>
  </div>
  <div class="legal">
    <span>Copyright &copy; 2016 &nbsp;SkyLoftReels. &nbsp;All rights reserved.</span>
    <div class="social" aria-label="Social links"><span></span><span></span><span></span><span></span></div>
  </div>
</footer>

</div>
</body>
</html>
```